German Headhunter/ HR Consultancy needs Business Cards Design

We need a business Card Design for our Company in Stuttgart. We are specialized as Headhunter/ HR Consultancy in Placement of specialist and managers in permanent employment. Please refer to our business logo.

```html
<!DOCTYPE html>
<html lang="en">
<head>
<meta charset="utf-8">
<title>Vantis Personalberatung – Business Card</title>
<link href="https://fonts.googleapis.com/css2?family=Karla:wght@400;500;700&display=swap" rel="stylesheet">
<style>
  :root {
    --page-bg: #d9d3cb;
    --navy-deep: #0c1450;
    --navy: #1b2a8a;
    --navy-soft: #33448f;
    --frost: #e4e6ea;
    --frost-edge: #c9ccd3;
    --stripe-dark: #4a4d55;
    --stripe-light: #f4f5f7;
    --text-light: #e9e6df;
    --brand-navy: #1a2466;
  }
  * { margin: 0; padding: 0; box-sizing: border-box; }
  html, body {
    width: 1200px;
    height: 969px;
    overflow: hidden;
    background: var(--page-bg);
    font-family: "Karla", sans-serif;
  }
  .card {
    position: absolute;
    left: 100px;
    top: 198px;
    width: 1000px;
    height: 572px;
    border-radius: 22px;
    overflow: hidden;
    background: var(--frost);
    box-shadow: 0 10px 30px rgba(0,0,0,0.18);
  }
  .card-shapes {
    position: absolute;
    inset: 0;
  }
  .contact-block {
    position: absolute;
    left: 68px;
    top: 140px;
    color: var(--text-light);
  }
  .person-name {
    font-size: 29px;
    font-weight: 500;
    letter-spacing: 1.5px;
    line-height: 1.1;
  }
  .person-role {
    font-size: 20px;
    letter-spacing: 0.6px;
    margin-top: 2px;
  }
  .address {
    font-size: 20.5px;
    letter-spacing: 0.6px;
    line-height: 28px;
    margin-top: 16px;
  }
  .contact-list {
    list-style: none;
    margin-top: 14px;
  }
  .contact-list li {
    display: flex;
    align-items: center;
    font-size: 20.5px;
    letter-spacing: 0.6px;
    height: 28.5px;
  }
  .contact-list svg {
    width: 18px;
    height: 18px;
    margin-right: 17px;
    fill: var(--text-light);
  }
  .brand {
    position: absolute;
    left: 530px;
    top: 246px;
    display: flex;
    align-items: center;
    color: var(--brand-navy);
    font-weight: 700;
  }
  .brand-square {
    width: 58px;
    height: 58px;
    background: var(--brand-navy);
    margin-right: 20px;
  }
  .brand-name {
    font-size: 50px;
    letter-spacing: 2px;
    line-height: 1;
  }
  .brand-sub {
    font-size: 19.5px;
    letter-spacing: 0.4px;
    line-height: 1;
    margin-top: 4px;
  }
</style>
</head>
<body>
  <div class="card">
    <svg class="card-shapes" viewBox="0 0 1000 572" width="1000" height="572" aria-hidden="true">
      <defs>
        <linearGradient id="navyPanel" x1="0" y1="0" x2="1" y2="1">
          <stop offset="0" stop-color="#3a4a96"/>
          <stop offset="0.45" stop-color="#253586"/>
          <stop offset="1" stop-color="#0d1556"/>
        </linearGradient>
        <linearGradient id="frostPanel" x1="0" y1="0" x2="1" y2="1">
          <stop offset="0" stop-color="#dcdfe5"/>
          <stop offset="1" stop-color="#eceef1"/>
        </linearGradient>
      </defs>
      <rect class="frost-panel" width="1000" height="572" fill="url(#frostPanel)"/>
      <polyline class="stripe-light" points="690,-10 404,286 690,582" fill="none" stroke="var(--stripe-light)" stroke-width="22"/>
      <polyline class="stripe-dark" points="676,-10 390,286 676,582" fill="none" stroke="var(--stripe-dark)" stroke-width="9"/>
      <polygon class="navy-panel" points="0,0 660,0 372,286 660,572 0,572" fill="url(#navyPanel)"/>
    </svg>

    <div class="contact-block">
      <div class="person-name">JONAS WEBER</div>
      <div class="person-role">Founder &amp; CEO</div>
      <div class="address">4120 Birchwood Lane<br>Fairbanks, Alaska 34718</div>
      <ul class="contact-list">
        <li><svg viewBox="0 0 24 24"><path d="M6.6 10.8a15.1 15.1 0 0 0 6.6 6.6l2.2-2.2a1 1 0 0 1 1-.25 11.4 11.4 0 0 0 3.6.57 1 1 0 0 1 1 1V20a1 1 0 0 1-1 1A17 17 0 0 1 3 4a1 1 0 0 1 1-1h3.5a1 1 0 0 1 1 1c0 1.25.2 2.45.57 3.57a1 1 0 0 1-.25 1z"/></svg>936-512-7830</li>
        <li><svg viewBox="0 0 24 24"><path d="M7 1h10a2 2 0 0 1 2 2v18a2 2 0 0 1-2 2H7a2 2 0 0 1-2-2V3a2 2 0 0 1 2-2zm0 3v14h10V4z"/></svg>936-274-9106</li>
        <li><svg viewBox="0 0 24 24"><path d="M6 2h9l3 3v5H6zM3 11h18v8H3zm3 5v6h12v-6z"/></svg>936-385-6420</li>
        <li><svg viewBox="0 0 24 24"><path d="M2 5h20v14H2zm2 2v.5l8 5 8-5V7zm0 3v7h16v-7l-8 5z"/></svg>jonas@vantispartner.com</li>
        <li><svg viewBox="0 0 24 24"><path d="M12 2a10 10 0 1 0 0 20 10 10 0 0 0 0-20zm-1 17.9A8 8 0 0 1 4.1 10.9L9 15v1a2 2 0 0 0 2 2zm6.9-2.5A2 2 0 0 0 16 16h-1v-3a1 1 0 0 0-1-1H8v-2h2a1 1 0 0 0 1-1V7h2a2 2 0 0 0 2-2v-.4a8 8 0 0 1 2.9 12.8z"/></svg>www.vantispartner.com</li>
      </ul>
    </div>

    <div class="brand">
      <div class="brand-square"></div>
      <div class="brand-text">
        <div class="brand-name">VANTIS</div>
        <div class="brand-sub">PERSONALBERATUNG</div>
      </div>
    </div>
  </div>
</body>
</html>
```